Postcard for Antique Furniture Restorer

My business is to restore antique furniture. I am based in Sydney, Australia.

I will be using this postcard to promote my business.
I will give it to customers like a With Compliments card.

Sometimes I will be writing information on the back of the card.

Design for Postcard Size eg 148 X 105mm

Front of card:

Attached are images of Antique furniture - please use ONLY 1 of the 3 images.
Deep etch the image on a white or cream background.

On front of card add these words:
Grainward Keepsakes
antique furniture restoration

Antiques travel through time, seeing generations of families
Through time they remain - they tell a continuing story
Be part of the journey

Back of postcard:
(leave space for notes to be handwritten)

Add these words:

Grainward Keepsakes
Corin Maddaford
mobile 0473 582 316
www.oakmendcraftery.com.au

Industry/Entity Type

Business

Font styles to use
Serif
Sans Serif

Colors
fefdec
ffffff

Requirements
Must have
• Use only 1 image. Image must be deep etched.

```html
<!DOCTYPE html>
<html lang="en">
<head>
<meta charset="utf-8">
<title>Grainward Keepsakes – Postcard</title>
<link rel="stylesheet" href="https://fonts.googleapis.com/css2?family=Alegreya+Sans:wght@500;700&family=Alegreya:ital,wght@0,400;0,700;1,400&display=swap">
<style>
  :root {
    --stage: #3b3b3b;
    --parchment-light: #f3e6c8;
    --parchment-mid: #e2c99a;
    --parchment-edge: #b98d55;
    --cream: #f1ebdc;
    --cream-deep: #e8dfca;
    --ink: #5a2c10;
    --ink-soft: #6b4426;
    --wood-light: #b4543a;
    --wood-dark: #5e1f14;
    --flourish: rgba(255, 253, 240, 0.55);
  }
  * { margin: 0; padding: 0; box-sizing: border-box; }
  html, body { width: 1200px; height: 560px; overflow: hidden; background: var(--stage); }
  .canvas {
    position: relative; width: 1200px; height: 560px;
    display: flex; gap: 40px; align-items: center; justify-content: center;
  }
  .card { position: relative; width: 540px; height: 383px; overflow: hidden; }

  /* Front */
  .card-front {
    background: radial-gradient(ellipse at 40% 40%, var(--parchment-light) 0%, var(--parchment-mid) 70%, var(--parchment-edge) 100%);
    clip-path: polygon(0 0, 100% 0, 100% 78%, 97% 84%, 93% 83%, 88% 90%, 82% 88%, 76% 94%, 68% 92%, 60% 97%, 52% 94%, 44% 98%, 36% 95%, 28% 99%, 20% 96%, 12% 100%, 5% 97%, 0 99%);
  }
  .front-flourish {
    position: absolute; left: 60px; top: 190px; width: 300px; height: 170px;
    background: radial-gradient(ellipse, var(--flourish) 0%, transparent 70%);
  }
  .front-flourish-top {
    position: absolute; left: 170px; top: 10px; width: 160px; height: 90px;
    background: radial-gradient(ellipse, var(--flourish) 0%, transparent 70%);
  }
  .armoire {
    position: absolute; left: 291px; top: 25px; width: 217px; height: 312px;
    background: linear-gradient(90deg, var(--wood-dark) 0%, var(--wood-light) 30%, var(--wood-light) 70%, var(--wood-dark) 100%);
  }
  .front-copy {
    position: absolute; left: 0; top: 70px; width: 290px; text-align: center; color: var(--ink);
  }
  .brand-name {
    font-family: "Alegreya Sans", sans-serif; font-weight: 700; font-size: 27px; line-height: 1;
  }
  .brand-tagline {
    font-family: "Alegreya Sans", sans-serif; font-weight: 500; font-size: 16.5px; margin-top: 7px;
  }
  .story {
    font-family: "Alegreya", serif; font-style: italic; font-size: 14px; line-height: 20px;
    margin-top: 10px; color: var(--ink-soft);
  }
  .call {
    font-family: "Alegreya", serif; font-size: 14.5px; margin-top: 4px;
  }

  /* Back */
  .card-back {
    background: linear-gradient(160deg, var(--cream) 0%, var(--cream-deep) 100%);
  }
  .back-flourish-top {
    position: absolute; left: 0; top: 0; width: 260px; height: 130px;
    background: radial-gradient(ellipse at 30% 30%, rgba(255,255,255,0.7) 0%, transparent 70%);
  }
  .back-flourish-bottom {
    position: absolute; left: 0; top: 250px; width: 290px; height: 133px;
    background: radial-gradient(ellipse at 40% 60%, rgba(255,255,255,0.7) 0%, transparent 70%);
  }
  .back-copy {
    position: absolute; left: 0; top: 127px; width: 284px; text-align: center; color: var(--ink);
  }
  .back-copy .brand-name { font-size: 23px; }
  .back-copy .brand-tagline { font-size: 15px; margin-top: 6px; }
  .contact-name {
    font-family: "Alegreya", serif; font-style: italic; font-size: 18px; margin-top: 14px; color: var(--ink-soft);
  }
  .contact-phone {
    font-family: "Alegreya", serif; font-weight: 700; font-size: 17px; margin-top: 2px;
  }
  .contact-web {
    font-family: "Alegreya", serif; font-weight: 700; font-size: 12.5px; margin-top: 2px;
  }
</style>
</head>
<body>
<main class="canvas">
  <section class="card card-front" aria-label="Postcard front">
    <div class="front-flourish-top" role="img" aria-label="Faint cream floral flourish"></div>
    <div class="front-flourish" role="img" aria-label="Faint cream floral flourish"></div>
    <div class="armoire" role="img" aria-label="Deep-etched photograph of a carved antique wooden armoire"></div>
    <div class="front-copy">
      <h1 class="brand-name">Grainward Keepsakes</h1>
      <p class="brand-tagline">Antique Furniture Restoration</p>
      <p class="story">Antiques travel through time, seeing<br>generations of families<br>Through time they remain - they tell a<br>continuing story</p>
      <p class="call">Be part of the journey</p>
    </div>
  </section>

  <section class="card card-back" aria-label="Postcard back">
    <div class="back-flourish-top" role="img" aria-label="Faint white floral flourish"></div>
    <div class="back-flourish-bottom" role="img" aria-label="Faint white floral flourish"></div>
    <div class="back-copy">
      <h2 class="brand-name">Grainward Keepsakes</h2>
      <p class="brand-tagline">Antique Furniture Restoration</p>
      <p class="contact-name">Corin Maddaford</p>
      <p class="contact-phone">0473 582 316</p>
      <p class="contact-web">www.oakmendcraftery.com.au</p>
    </div>
  </section>
</main>
</body>
</html>
```